Letterhead That Inspires Trust

Harbor Deed Remedies, LLC, (HDR) fixes technical problems with property deeds. The problems usually surface when someone tries to buy, sell or mortgage a piece of real estate and one of the lawyers involved find a title defect (a lien, an undischarged mortgage, a deceased person still on the title, unpaid taxes, etc.). HDR then gets involved and often has to contact prior property owners to get them to sign paperwork fixing the problem. We need a letterhead that will a) convey the seriousness of what we are trying to do, b) cause the recipients of our letters to recognize the importance of what are trying to do, and c) convey that we are a established and trustworthy company. We want it to include an image that suggests we are a problem solving company. Attached is an image we think might work; you can use it or not. In addition to our name (Harbor Deed Remedies, LLC), the letterhead must include our address and phone number: 418 Alder Lane, Suite 207, Lakeport, RI 02941 (401) 555-3827. We are thinking something straightforward without unnecessary colors or graphics.

```html
<!DOCTYPE html>
<html lang="en">
<head>
<meta charset="utf-8">
<title>Harbor Deed Remedies Letterhead</title>
<link rel="stylesheet" href="https://fonts.googleapis.com/css2?family=Arimo:wght@400&family=Montserrat:wght@600&family=Roboto:wght@400;500&family=Pinyon+Script&display=swap">
<style>
  :root {
    --backdrop: #e4e4e4;
    --paper: #f3f3f3;
    --ink: #1a1a1a;
    --brand-grey: #6e6e6e;
    --contact-grey: #7a7a7a;
    --footer-dark: #2e2d2e;
    --footer-line: #7d7d7d;
  }
  * { margin: 0; padding: 0; box-sizing: border-box; }
  html, body {
    width: 1200px; height: 1200px; overflow: hidden;
    background: var(--backdrop);
  }
  .letterhead {
    position: absolute; left: 204px; top: 40px;
    width: 792px; height: 1120px;
    background: var(--paper);
    box-shadow: 0 2px 10px rgba(0,0,0,0.12);
    overflow: hidden;
  }
  .brand {
    position: absolute; left: 72px; top: 64px;
    font-family: "Montserrat", sans-serif; font-weight: 600;
    font-size: 15px; line-height: 19px; letter-spacing: 0.3px;
    color: var(--brand-grey); text-transform: uppercase;
  }
  .contact {
    position: absolute; left: 541px; top: 67px;
    border-left: 3px solid var(--brand-grey);
    padding-left: 15px;
    font-family: "Roboto", sans-serif; font-size: 13px; line-height: 16px;
    font-style: normal;
    color: var(--contact-grey);
  }
  .contact .phone { font-weight: 500; display: flex; align-items: center; gap: 4px; }
  .contact .phone svg { width: 10px; height: 10px; fill: var(--contact-grey); }
  .letter {
    position: absolute; left: 85px; top: 264px; width: 624px;
    font-family: "Arimo", sans-serif; font-size: 13.3px; line-height: 18.6px;
    color: var(--ink);
  }
  .letter .date { margin-bottom: 19px; }
  .letter .recipient { margin-bottom: 37px; }
  .letter .salutation { margin-bottom: 18.6px; }
  .letter .body p { text-align: justify; margin-bottom: 18.6px; }
  .letter .closing { margin-top: 52px; }
  .letter .signature {
    font-family: "Pinyon Script", cursive; font-size: 24px; line-height: 30px;
    margin-top: 6px;
  }
  .footer-band { position: absolute; left: 0; top: 1020px; width: 792px; height: 100px; }
</style>
</head>
<body>
  <main class="letterhead">
    <header>
      <div class="brand">Harbor<br>Deed<br>Remedies</div>
      <address class="contact">
        <div class="phone">
          <svg viewBox="0 0 24 24" aria-hidden="true"><path d="M6.6 10.8a15.1 15.1 0 0 0 6.6 6.6l2.2-2.2a1 1 0 0 1 1-.25 11.4 11.4 0 0 0 3.6.57 1 1 0 0 1 1 1V20a1 1 0 0 1-1 1A17 17 0 0 1 3 4a1 1 0 0 1 1-1h3.5a1 1 0 0 1 1 1c0 1.25.2 2.45.57 3.57a1 1 0 0 1-.25 1z"/></svg>
          (401) 555-3827
        </div>
        <div>418 Alder Lane, Suite 207</div>
        <div>Lakeport, RI 02941</div>
      </address>
    </header>

    <section class="letter">
      <p class="date">01 January 2050</p>
      <p class="recipient">Northgate Holdings Ltd.<br>PO Box 4120 Elmcrest Rd<br>Riverton City Country 4120</p>
      <p class="salutation">Dear Martin Ashby,</p>
      <div class="body">
        <p>Lorem ipsum dolor sit amet, consectetuer adipiscing elit, sed diam nonummy nibh euismod tincidunt ut laoreet dolore magna aliquam erat volutpat. Ut wisi enim ad minim veniam, quis nostrud exerci tation ullamcorper suscipit lobortis nisl ut aliquip ex ea commodo consequat. Duis dolore te feugait nulla facilisi. Nam liber tempor cum soluta nobis eleifend option congue nihil imperdiet doming id quod mazim placerat facer possim assum. Lorem ipsum dolor sit amet, consectetuer adipiscing elit, sed diam nonummy nibh euismod tincidunt ut laoreet dolore magna aliquam erat volutpat. Ut wisi enim ad minim veniam, quis nostrud exerci tation ullamcorper suscipit lobortis nisl ut aliquip ex ea commodo consequat.</p>
        <p>Consectetuer adipiscing elit, sed diam nonummy nibh euismod tincidunt ut laoreet dolore magna aliquam erat volutpat. Ut wisi enim ad minim veniam, quis nostrud exerci tation ullamcorper suscipit lobortis nisl ut aliquip ex ea commodo consequat. Consectetuer adipiscing elit, sed diam nonummy nibh euismod tincidunt ut laoreet dolore magna aliquam erat volutpat. Ut wisi enim ad minim veniam, quis nostrud exerci tation ullamcorper suscipit lobortis nisl ut aliquip ex ea commodo consequat.</p>
        <p>Consectetuer adipiscing elit, sed diam nonummy nibh euismod tincidunt ut laoreet dolore magna aliquam erat volutpat. Ut wisi enim ad minim veniam, quis nostrud exerci tation ullamcorper suscipit lobortis nisl ut aliquip ex ea commodo consequat. Consectetuer adipiscing elit, sed diam nonummy nibh euismod tincidunt ut laoreet dolore magna aliquam erat volutpat. Ut wisi enim ad minim veniam, quis nostrud exerci tation ullamcorper suscipit lobortis nisl ut aliquip ex ea commodo consequat.</p>
      </div>
      <p class="closing">Sincerely Yours</p>
      <p class="signature">Daniel Whitford</p>
    </section>

    <svg class="footer-band" viewBox="0 0 792 100" preserveAspectRatio="none" aria-hidden="true">
      <path d="M0,9 Q396,132 792,12 L792,21 Q396,140 0,20 Z" fill="var(--footer-line)"/>
      <path d="M0,26 Q396,138 792,24 L792,100 L0,100 Z" fill="var(--footer-dark)"/>
    </svg>
  </main>
</body>
</html>
```